New Dental Office Needs an Attractive and user friendly Website Designed

I need a website for a new dental office. The Name is Harrowfield Dentistry. I would like a Modern design with a user friendly interface and usability.
I would like a landing page, a page that lists the services we offer: Cosmetic Dentistry, Implants, Dental Hygiene, Emergency Services, Restorations, Dentures
Target Market(s)
Mid to upper class
Industry/Entity Type
Dentistry
Coding
Number of Pages Required
1 page
Requirements
Must have
- Landing page that has a scheduling option, Procedures, operating hours, and contact us info
Nice to have
- Appealing design, Soft comforting colors. Easy to navigate page, Modern and professional.

```html
<!DOCTYPE html>
<html lang="en">
<head>
<meta charset="utf-8">
<title>Harrowfield Dentistry</title>
<link rel="stylesheet" href="https://fonts.googleapis.com/css2?family=Poppins:wght@300;400;500;600&display=swap">
<style>
:root{
  --teal:#457b80;
  --navy:#0c2a4d;
  --ink:#1f2a33;
  --muted:#5d6770;
  --paper:#f5f5f2;
  --card-tint:#d7e6e7;
  --white:#ffffff;
  --line:#d9dde0;
}
*{box-sizing:border-box;margin:0;padding:0}
html,body{width:1200px;height:3796px;overflow:hidden}
body{font-family:"Poppins",sans-serif;background:var(--paper);color:var(--ink);position:relative}
.abs{position:absolute}
.btn{position:absolute;display:flex;align-items:center;justify-content:center;border-radius:20px;font-size:12px;font-weight:500;color:var(--white)}
.btn-navy{background:var(--navy)}
.btn-teal{background:var(--teal)}
.eyebrow{font-size:13px;color:var(--teal)}
.center{left:0;width:1200px;text-align:center}

/* header & hero */
.hero{top:0;left:0;width:1200px;height:649px;background:linear-gradient(100deg,#f3f3f4 0%,#eceef0 40%,#d9dfe4 62%,#b8c3cc 80%,#8c9bb0 100%)}
.hero-photo{top:0;left:0;width:1200px;height:649px;background:radial-gradient(ellipse at 78% 40%,rgba(120,130,150,.35),transparent 55%),radial-gradient(ellipse at 25% 95%,rgba(200,190,200,.55),transparent 50%)}
.logo{top:30px;left:160px;font-size:18px;font-weight:500;color:var(--navy);white-space:nowrap}
.nav{top:25px;left:395px;width:427px;height:38px;background:var(--white);border-radius:19px;display:flex;align-items:center;justify-content:space-around;padding:0 18px;font-size:12px;color:var(--ink)}
.nav .active{color:var(--teal);border-bottom:2px solid var(--teal);padding:10px 0 6px;margin-top:4px}
.hero h1{top:222px;left:160px;font-size:47px;font-weight:600;line-height:59px;color:var(--navy)}
.hero h1 span{color:var(--teal);font-size:55px;display:block}
.hero-sub{top:352px;left:160px;width:440px;font-size:14.5px;line-height:18px;color:var(--muted)}
.quote-name{top:445px;left:900px;width:180px;height:33px;background:var(--white);border-radius:17px;display:flex;align-items:center;gap:10px;padding-left:8px;font-size:14px;color:var(--navy)}
.quote-name i{width:22px;height:22px;border-radius:50%;background:#c8ced4;display:block}
.quote-card{top:497px;left:702px;width:373px;height:101px;background:var(--teal);border-radius:14px;color:var(--white);font-size:13px;line-height:16px;padding:26px 26px 0 34px}
.quote-mark{top:482px;left:1012px;font-size:40px;color:#e7b54a;font-weight:600}
.hero-dots{top:623px;left:882px;width:34px;height:2px;background:var(--white)}

/* about */
.about-h{top:733px;font-size:30px;font-weight:600;line-height:37px;color:var(--ink)}
.about-p{top:824px;left:228px;width:744px;text-align:center;font-size:13.5px;line-height:19.5px;color:var(--ink)}

/* services */
.services{top:1051px;left:0;width:1200px;height:615px;overflow:hidden;background:linear-gradient(180deg,#4f8287,#4a7d82 60%,#54878c)}
.services .eyebrow,.testi .eyebrow{color:#e8f0f0}
.sec-h{font-size:31px;font-weight:600;color:var(--white)}
.sec-sub{font-size:13.5px;line-height:19px;color:#e3eced}
.svc{top:215px;width:260px;height:222px;background:var(--white);border-radius:4px;padding:18px 24px}
.svc .ico{width:56px;height:56px;border-radius:50%;border:3px solid #cfe1e2;display:flex;align-items:center;justify-content:center;background:#f0f6f6;margin-left:-8px}
.svc h3{font-size:16.5px;font-weight:500;margin-top:12px;color:var(--ink)}
.svc p{font-size:11px;line-height:16px;color:var(--muted);margin-top:6px}
.svc a{display:block;font-size:11px;color:var(--teal);margin-top:14px}
.dots{top:473px;left:583px;display:flex;gap:6px;align-items:center}
.dots i{width:5px;height:5px;border-radius:50%;background:var(--white);display:block}
.dots i.on{width:12px;height:12px;border:3px solid var(--white);background:transparent}

/* team & faq */
.team-h{top:1746px;left:160px;font-size:30px;font-weight:600;color:var(--ink)}
.doc{width:202px;height:245px;border-radius:2px;overflow:hidden}
.doc .tag{position:absolute;left:16px;right:16px;bottom:16px;height:58px;background:var(--white);border-radius:6px;text-align:center;padding-top:10px}
.doc .tag b{display:block;font-size:14.5px;font-weight:500}
.doc .tag span{font-size:11px;color:var(--muted)}
.faq{top:1724px;left:611px;width:426px;height:620px;background:var(--white);border-radius:14px;padding:30px 30px 0}
.faq h2{font-size:23px;font-weight:600;line-height:27px;margin-bottom:18px}
.faq-item{height:71px;display:flex;align-items:center;justify-content:space-between;border-bottom:2px solid var(--line);font-size:12.5px;color:var(--ink)}
.faq-item:last-child{border-bottom:none}
.faq-item em{font-style:normal;font-size:20px;font-weight:300}

/* testimonials */
.testi{top:2434px;left:0;width:1200px;height:452px;background:var(--teal);overflow:hidden}
.tcard{top:199px;width:254px;height:253px;background:var(--card-tint);padding:26px 26px 0}
.tcard .stars{font-size:21px;color:var(--teal);letter-spacing:2px}
.tcard h4{font-size:15px;font-weight:500;line-height:18px;margin-top:12px;color:var(--ink)}
.tcard p{font-size:11px;line-height:17px;color:var(--muted);margin-top:12px}
.tcard p u{color:var(--teal)}
.tcard .who{margin-top:16px;font-size:14px;color:var(--ink)}
.tcard .who small{display:block;font-size:11.5px;color:var(--teal)}
.arrow{width:32px;height:32px;border-radius:50%;border:1px solid var(--muted);display:flex;align-items:center;justify-content:center;background:var(--white)}
.track{top:2947px;left:397px;width:406px;height:7px;border-radius:4px;background:#c9d7d8}
.track i{position:absolute;left:53px;width:128px;height:7px;border-radius:4px;background:var(--navy);display:block}

/* contact */
.photo-l{top:3041px;left:0;width:360px;height:445px;background:linear-gradient(150deg,#c99a86,#e4c2b2 45%,#9c94c8 80%,#7e77b8)}
.photo-r{top:3041px;left:840px;width:360px;height:445px;background:linear-gradient(120deg,#b9bcbf,#e8e9ea 45%,#c5cacd 70%,#8fd0d9)}
.form{top:3041px;left:360px;width:480px;height:445px;background:var(--white)}
.form h2{position:absolute;top:56px;width:480px;text-align:center;font-size:29px;font-weight:500}
.field{position:absolute;width:177px;border-bottom:1px solid var(--line);font-size:11px;color:#8a9197;padding-bottom:12px}

/* footer */
.footer{top:3486px;left:0;width:1200px;height:310px;background:var(--navy);color:var(--white)}
.flogo{top:34px;font-size:28px;font-weight:500}
.fnav{top:109px;left:380px;width:450px;display:flex;justify-content:space-between;font-size:12px}
.contact-row{top:153px;left:200px;width:800px;display:flex;justify-content:space-between;font-size:12px;align-items:center}
.contact-row span{display:flex;align-items:center;gap:10px}
.cicon{width:26px;height:26px;border-radius:50%;background:var(--teal);display:flex;align-items:center;justify-content:center}
.social{top:208px;left:549px;display:flex;gap:30px}
.social i{width:12px;height:12px;border-radius:50%;border:1.5px solid var(--white);display:block}
.frule{top:256px;left:160px;width:877px;height:1px;background:#36506f}
.copy{top:278px;font-size:11px}
</style>
</head>
<body>

<section class="hero abs">
  <div class="hero-photo abs" role="img" aria-label="Dentist in protective glasses treating a patient in the clinic chair"></div>
  <div class="logo abs">Harrowfield Dentistry</div>
  <nav class="nav abs"><span class="active">Home</span><span>About Us</span><span>Services</span><span>Dentists</span><span>Contact Us</span></nav>
  <a class="btn btn-teal" style="top:24px;left:877px;width:160px;height:39px">Book Appointment</a>
  <h1 class="abs">High Quality and <span>Painless Dentistry</span></h1>
  <p class="hero-sub abs">If you are in need of high-quality, professional and friendly dental care, look no further than our clinic.</p>
  <a class="btn btn-navy" style="top:409px;left:160px;width:161px;height:38px">Learn More</a>
  <div class="quote-name abs"><i></i>Maya Ellison</div>
  <div class="quote-card abs">“If you are in need of high-quality, professional and friendly dental care, look no further than our clinic.”</div>
  <div class="quote-mark abs">”</div>
  <div class="hero-dots abs"></div>
</section>

<section>
  <p class="eyebrow abs center" style="top:705px">About Us</p>
  <h2 class="about-h abs center">Professionals and Personalized<br>Dental Excellence</h2>
  <p class="about-p abs">It is a long established fact that a reader will be distracted by the readable content of a page when looking at its layout. The point of using Lorem Ipsum is that it has a more-or-less normal distribution of letters, as opposed to using 'Content here, content here', making it look like readable English. Many desktop publishing packages and web page editors now use Lorem Ipsum as their default model text, and a search for 'lorem ipsum' will uncover many web sites still in their infancy.</p>
  <a class="btn btn-teal" style="top:951px;left:519px;width:161px;height:39px">Learn More</a>
</section>

<section class="services abs">
  <p class="eyebrow abs center" style="top:58px">Our Services</p>
  <h2 class="sec-h abs center" style="top:80px">Complete Care for Every Smile</h2>
  <p class="sec-sub abs center" style="top:133px">Welcome to our Harrowfield practice, dedicated to giving every patient<br>valuable knowledge and resources.</p>
  <div class="svc abs" style="left:55px"><div class="ico"><svg width="26" height="26" viewBox="0 0 26 26" fill="none" stroke="#457b80" stroke-width="1.5"><path d="M6 5c3-2 5 0 7 0s4-2 7 0c2 2 1 7-1 10l-1 7-2 0-1-6-2 0-1 6-2 0-1-7C5 12 4 7 6 5z"/></svg></div><h3>Cosmetic Dentistry</h3><p>It is a long established fact that a reader will be distracted by when looking at its layout.</p><a>LEARN MORE</a></div>
  <div class="svc abs" style="left:332px"><div class="ico"><svg width="26" height="26" viewBox="0 0 26 26" fill="none" stroke="#457b80" stroke-width="1.5"><path d="M7 4h12v5H7z"/><path d="M9 9h8M10 12h6M10 15h6M11 18h4M12 21h2"/></svg></div><h3>Implants</h3><p>It is a long established fact that a reader will be distracted by when looking at its layout.</p><a>LEARN MORE</a></div>
  <div class="svc abs" style="left:608px"><div class="ico"><svg width="26" height="26" viewBox="0 0 26 26" fill="none" stroke="#457b80" stroke-width="1.5"><path d="M5 22L17 6M15 4l4 4"/><path d="M14 14c2-2 5-1 6 1s0 6-2 7"/></svg></div><h3>Dental Hygiene</h3><p>It is a long established fact that a reader will be distracted by when looking at its layout.</p><a>LEARN MORE</a></div>
  <div class="svc abs" style="left:885px"><div class="ico"><svg width="26" height="26" viewBox="0 0 26 26" fill="none" stroke="#457b80" stroke-width="1.5"><rect x="4" y="8" width="18" height="10" rx="4"/><path d="M8 8v10M13 8v10M18 8v10M4 13h18"/></svg></div><h3>Emergency Services</h3><p>It is a long established fact that a reader will be distracted by when looking at its layout.</p><a>LEARN MORE</a></div>
  <div class="svc abs" style="left:1220px"><div class="ico"><svg width="26" height="26" viewBox="0 0 26 26" fill="none" stroke="#457b80" stroke-width="1.5"><path d="M6 5c3-2 5 0 7 0s4-2 7 0c2 2 1 7-1 10l-1 7-2 0-1-6-2 0-1 6-2 0-1-7C5 12 4 7 6 5z"/><path d="M10 9h6"/></svg></div><h3>Restorations</h3><p>It is a long established fact that a reader will be distracted by when looking at its layout.</p><a>LEARN MORE</a></div>
  <div class="svc abs" style="left:1497px"><div class="ico"><svg width="26" height="26" viewBox="0 0 26 26" fill="none" stroke="#457b80" stroke-width="1.5"><path d="M4 10c4-4 14-4 18 0v4c-4 4-14 4-18 0z"/><path d="M9 8v10M13 7v12M17 8v10"/></svg></div><h3>Dentures</h3><p>It is a long established fact that a reader will be distracted by when looking at its layout.</p><a>LEARN MORE</a></div>
  <div class="dots abs"><i></i><i class="on"></i><i></i></div>
  <a class="btn btn-navy" style="top:516px;left:520px;width:160px;height:39px">View All Services</a>
</section>

<section>
  <p class="eyebrow abs" style="top:1721px;left:160px">Meet Our Dental Team</p>
  <h2 class="team-h abs">Our Expert Dentist</h2>
  <div class="doc abs" style="top:1831px;left:160px;background:linear-gradient(160deg,#bcd4ec,#7fa8d6)" role="img" aria-label="Portrait of a smiling female dentist in blue scrubs"><div class="tag"><b>Dr. Clara Whitmore</b><span>Lead Dentist</span></div></div>
  <div class="doc abs" style="top:1831px;left:379px;background:linear-gradient(160deg,#a7aeb5,#d8dde1)" role="img" aria-label="Portrait of a male dentist in a white coat giving thumbs up"><div class="tag"><b>Dr. Clara Whitmore</b><span>Lead Dentist</span></div></div>
  <div class="doc abs" style="top:2099px;left:160px;background:linear-gradient(160deg,#6fd2df,#2fb0c4)" role="img" aria-label="Portrait of a female dentist holding dental tools"><div class="tag"><b>Dr. Clara Whitmore</b><span>Lead Dentist</span></div></div>
  <div class="doc abs" style="top:2099px;left:379px;background:linear-gradient(160deg,#b5bcc3,#e4e7ea)" role="img" aria-label="Portrait of a smiling male dentist in a white coat"><div class="tag"><b>Dr. Clara Whitmore</b><span>Lead Dentist</span></div></div>

  <div class="faq abs">
    <h2>Frequently Asked<br>Questions</h2>
    <div class="faq-item">Do you accept walk-ins?<em>+</em></div>
    <div class="faq-item">Do you accept dental insurance?<em>+</em></div>
    <div class="faq-item">Do you offer emergency dental services?<em>+</em></div>
    <div class="faq-item">How can I improve my oral hygiene routine?<em>+</em></div>
    <div class="faq-item">Do you accept walk-ins?<em>+</em></div>
    <div class="faq-item">How can I improve my oral hygiene routine?<em>+</em></div>
    <div class="faq-item">Do you accept walk-ins?<em>+</em></div>
  </div>
</section>

<section class="testi abs">
  <p class="eyebrow abs center" style="top:40px">Our Testimonial</p>
  <h2 class="sec-h abs center" style="top:64px">Pleasing Patients Is Our Greatest Achievement</h2>
  <p class="sec-sub abs center" style="top:115px">Welcome to our Harrowfield practice, dedicated to giving every patient<br>valuable knowledge and resources.</p>
  <div class="tcard abs" style="left:-64px"><div class="stars">★★★★★</div><h4>“This Whole Practice<br>Is Wonderful!!”</h4><p>It is a long established fact that a reader will be distracted by the of using Lorem Ipsum. <u>READ MORE</u></p><div class="who">Nora P.<small>Elm Ridge</small></div></div>
  <div class="tcard abs" style="left:204px"><div class="stars">★★★★★</div><h4>“This Whole Practice<br>Is Wonderful!!”</h4><p>It is a long established fact that a reader will be distracted by the of using Lorem Ipsum. <u>READ MORE</u></p><div class="who">Nora P.<small>Elm Ridge</small></div></div>
  <div class="tcard abs" style="left:473px"><div class="stars">★★★★★</div><h4>“This Whole Practice<br>Is Wonderful!!”</h4><p>It is a long established fact that a reader will be distracted by the of using Lorem Ipsum. <u>READ MORE</u></p><div class="who">Nora P.<small>Elm Ridge</small></div></div>
  <div class="tcard abs" style="left:741px"><div class="stars">★★★★★</div><h4>“This Whole Practice<br>Is Wonderful!!”</h4><p>It is a long established fact that a reader will be distracted by the of using Lorem Ipsum. <u>READ MORE</u></p><div class="who">Nora P.<small>Elm Ridge</small></div></div>
  <div class="tcard abs" style="left:1010px"><div class="stars">★★★★★</div><h4>“This Whole Practice<br>Is Wonderful!!”</h4><p>It is a long established fact that a reader will be distracted by the of using Lorem Ipsum. <u>READ MORE</u></p><div class="who">Nora P.<small>Elm Ridge</small></div></div>
</section>
<div class="arrow abs" style="top:2934px;left:326px"><svg width="10" height="10" viewBox="0 0 10 10"><path d="M6.5 1.5L3 5l3.5 3.5" fill="none" stroke="#1f2a33" stroke-width="1.5"/></svg></div>
<div class="track abs"><i></i></div>
<div class="arrow abs" style="top:2934px;left:841px"><svg width="10" height="10" viewBox="0 0 10 10"><path d="M3.5 1.5L7 5 3.5 8.5" fill="none" stroke="#1f2a33" stroke-width="1.5"/></svg></div>

<section>
  <div class="photo-l abs" role="img" aria-label="Close-up of a patient with braces during a dental check-up"></div>
  <div class="form abs">
    <p class="eyebrow" style="position:absolute;top:40px;width:480px;text-align:center">Contact</p>
    <h2>Get In Touch</h2>
    <div class="field" style="top:138px;left:42px">Name*</div>
    <div class="field" style="top:138px;left:258px">Company Name</div>
    <div class="field" style="top:200px;left:42px">Phone</div>
    <div class="field" style="top:200px;left:258px">Email Address*</div>
    <div class="field" style="top:262px;left:42px;width:393px;height:75px">Your Message</div>
    <a class="btn btn-teal" style="top:368px;left:138px;width:204px;height:37px">SUBMIT</a>
  </div>
  <div class="photo-r abs" role="img" aria-label="Soft-focus dental clinic equipment with blue tones"></div>
</section>

<footer class="footer abs">
  <div class="flogo abs center">Harrowfield Dentistry</div>
  <nav class="fnav abs"><span>Home</span><span>About Us</span><span>Services</span><span>Team</span><span>Contact Us</span></nav>
  <div class="contact-row abs">
    <span><i class="cicon"><svg width="12" height="12" viewBox="0 0 12 12"><path d="M3 1l2 2-1 1.5c.7 1.5 2 2.8 3.5 3.5L9 7l2 2-1.5 2C5 10.5 1.5 7 1 2.5z" fill="#fff"/></svg></i>+1 555 014 2290</span>
    <span><i class="cicon"><svg width="12" height="12" viewBox="0 0 12 12"><rect x="1" y="2.5" width="10" height="7" rx="1" fill="#fff"/><path d="M1.5 3l4.5 3.5L10.5 3" fill="none" stroke="#457b80"/></svg></i>hello@harrowfielddental.com</span>
    <span><i class="cicon"><svg width="12" height="12" viewBox="0 0 12 12"><path d="M6 11S2 7 2 4.5a4 4 0 018 0C10 7 6 11 6 11z" fill="#fff"/><circle cx="6" cy="4.5" r="1.4" fill="#457b80"/></svg></i>122 Maple Court, Elm Ridge</span>
    <span><i class="cicon"><svg width="12" height="12" viewBox="0 0 12 12"><circle cx="6" cy="6" r="4.5" fill="none" stroke="#fff" stroke-width="1.3"/><path d="M6 3.5V6l1.8 1.2" fill="none" stroke="#fff" stroke-width="1.3"/></svg></i>Mon–Sat 8am–6pm</span>
  </div>
  <div class="social abs"><i></i><i></i><i></i></div>
  <div class="frule abs"></div>
  <p class="copy abs center">Copyright © 2025 Harrowfield. All rights reserved.</p>
</footer>

</body>
</html>
```